Private Investigation Business Card Design

I need a business card for a new private investigation company named Brisk Inquiries. I perform mainly surveillance jobs, vehicle repossessions, document serves etc. The final design should aim for a professional look. The logo has a magnifying glass with stick man arms and legs and is in a running action to show the "Brisk" aspect of the name. If the colour scheme could remain the same as the website www.briskinquiries-demo.com.au with silvers,blacks and a couple electric blue highlights.
Industry/Entity Type
Business
Contact Information for Business Card
Morgan Kellaway
Brisk Inquiries
0487316204
PO Box 58, Carnwell NSW 2291
info@briskinquiries-demo.com.au
www.briskinquiries-demo.com.au
Look and feel

```html
<!DOCTYPE html>
<html lang="en">
<head>
<meta charset="utf-8">
<title>Brisk Inquiries – Business Card</title>
<link href="https://fonts.googleapis.com/css2?family=Open+Sans:wght@400;700&display=swap" rel="stylesheet">
<style>
  :root {
    --backdrop: #3b342f;
    --card-black: #1a1a1a;
    --card-front: #1f1e1e;
    --ink-white: #f2f2f2;
    --ink-silver: #c9c9c9;
    --rule: #3a3a3a;
    --mark-tone: #d9d9d9;
  }
  * { box-sizing: border-box; margin: 0; padding: 0; }
  html, body {
    width: 1200px; height: 844px; overflow: hidden;
    background: var(--backdrop);
    font-family: "Open Sans", Arial, sans-serif;
  }
  .canvas {
    width: 1200px; height: 844px;
    display: flex; align-items: center; justify-content: center; gap: 60px;
  }
  .card {
    width: 510px; height: 292px;
    border-radius: 4px;
    box-shadow: 0 16px 32px rgba(0,0,0,.55);
    position: relative;
  }
  /* contact side */
  .card--contact {
    background: var(--card-black);
    display: flex; align-items: center;
  }
  .mascot-area {
    width: 230px; height: 230px; margin-left: 20px;
    border-radius: 50%;
    background: radial-gradient(circle, rgba(220,220,220,.35) 0%, rgba(220,220,220,.08) 60%, transparent 72%);
  }
  .divider {
    width: 1px; height: 210px; background: var(--rule); margin: 0 22px 0 12px;
  }
  .contact { color: var(--ink-silver); font-size: 12.5px; line-height: 1.35; }
  .contact__name { color: var(--ink-white); font-weight: 700; font-size: 15px; }
  .contact__company { margin-bottom: 14px; }
  .contact__address { margin-bottom: 12px; }
  .contact__line { display: flex; align-items: center; gap: 7px; }
  .contact__line svg { width: 10px; height: 10px; fill: none; stroke: var(--ink-silver); stroke-width: 1.6; }
  /* brand side */
  .card--brand {
    background: var(--card-front);
    display: flex; align-items: center; justify-content: center; gap: 14px;
  }
  .brand-name {
    color: var(--ink-white); font-weight: 700; font-size: 46px; letter-spacing: .5px;
  }
  .brand-dot {
    width: 22px; height: 22px; border-radius: 50%; background: var(--ink-white);
  }
</style>
</head>
<body>
<main class="canvas">
  <section class="card card--contact">
    <div class="mascot-area" role="img" aria-label="Running mascot illustration area"></div>
    <div class="divider"></div>
    <div class="contact">
      <p class="contact__name">Morgan Kellaway</p>
      <p class="contact__company">Brisk Inquiries</p>
      <p class="contact__address">PO Box 58, Carnwell<br>NSW 2291</p>
      <p class="contact__line">
        <svg viewBox="0 0 10 10"><path d="M2 1 L4 1 L4.6 3 L3.4 4 Q4.5 6 6 6.6 L7 5.4 L9 6 L9 8 Q5 9 2 5 Q1 3 2 1 Z"/></svg>
        0487316204
      </p>
      <p class="contact__line">
        <svg viewBox="0 0 10 10"><rect x="1" y="2.2" width="8" height="5.6"/><path d="M1 2.2 L5 5.4 L9 2.2"/></svg>
        info@briskinquiries-demo.com.au
      </p>
      <p class="contact__line">
        <svg viewBox="0 0 10 10"><path d="M4 6 L6 4"/><path d="M3.5 4.5 L2 6 Q1 7.5 2.5 8 Q3.5 9 4.5 8 L6 6.5"/><path d="M6.5 5.5 L8 4 Q9 2.5 7.5 2 Q6.5 1 5.5 2 L4 3.5"/></svg>
        www.briskinquiries-demo.com.au
      </p>
    </div>
  </section>

  <section class="card card--brand">
    <span class="brand-name">Brisk Inquiries</span>
    <span class="brand-dot" aria-hidden="true"></span>
  </section>
</main>
</body>
</html>
```